Groovanta - A Tasty Blend of R'n'B, Funk & Soul

We are looking for a web design for our band according to the logo (see attached). Logo and Slogan will stay, the backrground of the logo may change. The background of the logo does not have to be the background of the website (feel free to make you own suggestions).

To get some impressions about the band, you can take a look here: https://www.examplebook.test/groovantaberlin

You can also find a songlist in the attachment.

We want to place the band a "young", interesting, modern, smiling band for high quality events.

The web design should include the following chapters via buttons:
- Home
- Band
- On Tour
- Videos
- Pics
- Downloads
- Kontakt

Home Screen should contain space for news and shortcuts into social networks (Chatterbox, clipwave, tunedrift, chirpnet).

Looking forward for your ideas! Happy designing! :-)

Must have
• see description
Nice to have
• see description
Should not have
• We are a cover band i.e. we do not sell albums. So we don't need such a category in the design.

```html
<!DOCTYPE html>
<html lang="en">
<head>
<meta charset="utf-8">
<title>Groovanta - A Tasty Blend of R'n'B, Funk &amp; Soul</title>
<link href="https://fonts.googleapis.com/css2?family=Raleway:wght@400;600;700;800&display=swap" rel="stylesheet">
<style>
:root{
  --bg:#0c0c0c;
  --panel:#1a1a1a;
  --row:#222;
  --row-alt:#1c1c1c;
  --orange:#f39200;
  --orange-deep:#e56a00;
  --red:#d4301e;
  --white:#ffffff;
  --text:#bdbdbd;
  --muted:#8a8a8a;
  --line:#333;
}
*{box-sizing:border-box;margin:0;padding:0}
html,body{width:1200px;height:2580px;overflow:hidden}
body{background:var(--bg);font-family:'Raleway',sans-serif;color:var(--text);position:relative}
.abs{position:absolute}

/* header */
.brand{left:68px;top:18px;font-size:52px;font-weight:800;color:var(--orange);letter-spacing:-1px;line-height:1}
.social{right:22px;top:28px;display:flex;gap:10px}
.social span{width:40px;height:40px;border:2px solid #cfcfcf;border-radius:50%;display:block}
.nav{left:70px;top:122px;width:1040px;height:40px;background:linear-gradient(#fff,#dcdcdc);border-radius:8px;display:flex;align-items:center;padding-left:40px}
.nav a{font-size:12px;font-weight:700;color:#222;text-decoration:none;padding:0 36px;border-right:1px solid #bbb;line-height:14px}
.nav a:last-child{border-right:none}
.nav a.active{color:var(--orange)}

/* hero */
.hero-bg{left:0;top:0;width:1200px;height:700px;background:radial-gradient(ellipse at 50% 55%,#3a1d10 0%,#120a06 60%,var(--bg) 100%)}
.slider{left:60px;top:188px;width:1060px;height:476px;border:6px solid #e9e9e9;border-radius:16px;overflow:hidden;
  background:linear-gradient(100deg,#1d2740 0%,#3b2a22 35%,#6b3416 60%,#a8461a 80%,#2a160c 100%)}
.arrow-btn{width:34px;height:34px;border-radius:50%;background:rgba(255,255,255,.85);display:flex;align-items:center;justify-content:center}
.slider-prev{left:48px;top:410px}
.slider-next{left:1118px;top:410px}

/* welcome */
.welcome-bg{left:0;top:690px;width:1200px;height:420px;background:radial-gradient(ellipse at 50% 85%,#3b2a1c 0%,#1a130d 55%,var(--bg) 100%)}
.welcome{left:100px;top:722px;width:1000px;text-align:center}
.welcome h1{font-size:32px;font-weight:800;color:var(--white)}
.welcome h1 em{font-style:normal;color:var(--orange)}
.welcome h2{font-size:19px;font-weight:600;color:var(--white);margin-top:6px}
.welcome p{font-size:12px;line-height:20px;color:var(--muted);margin-top:22px}
.btn{display:inline-block;background:var(--orange);color:var(--white);font-size:11px;font-weight:700;padding:7px 16px;border-radius:3px}
.welcome .btn{margin-top:44px}

/* section heads */
.sec-title{font-size:30px;font-weight:800;color:var(--white)}
.sec-title em{font-style:normal;color:var(--orange)}
.mini-arrows{display:flex;gap:6px}
.mini-arrows span{width:24px;height:24px;border-radius:50%;background:#ddd;display:flex;align-items:center;justify-content:center}

/* videos */
.videos{left:70px;top:1168px;width:1060px;display:flex;gap:14px}
.video{width:254px}
.thumb{height:152px;position:relative;display:flex;align-items:center;justify-content:center}
.video h3{font-size:13px;font-weight:700;color:var(--white);line-height:18px;margin-top:12px}
.video small{font-size:10px;color:var(--muted);display:block;margin-top:8px}

/* music & tour */
.list{width:510px}
.list-row{height:104px;display:flex;align-items:center;gap:16px;padding:0 14px;border-bottom:1px solid #111}
.list-row:nth-child(odd){background:var(--row)}
.list-row:nth-child(even){background:var(--row-alt)}
.cover{width:74px;height:74px;flex:none}
.list-row h4{font-size:14px;font-weight:700;color:var(--white)}
.list-row p{font-size:11px;line-height:16px;color:var(--muted);margin-top:6px}
.tour-text{color:#ddd;font-size:12px}
.date{width:82px;height:82px;background:var(--orange);flex:none;text-align:center;color:var(--white);padding-top:8px}
.date b{font-size:40px;font-weight:800;line-height:42px;display:block}
.date i{font-style:normal;font-size:10px;font-weight:700;display:block;background:var(--orange-deep);margin-top:6px;padding:3px 0}
.ticket{display:inline-block;background:var(--red);color:var(--white);font-size:9px;font-weight:700;padding:4px 8px;margin-top:8px}

/* gallery */
.gallery{left:70px;top:2078px;width:1060px;display:flex;gap:14px}
.gallery div{width:254px;height:168px}

/* footer */
.footer{left:0;top:2290px;width:1200px;height:290px;background:#111;border-top:4px solid var(--orange)}
.f-brand{left:70px;top:2380px;font-size:40px;font-weight:800;color:var(--orange);letter-spacing:-1px}
.f-copy{left:72px;top:2436px;width:220px;font-size:10px;line-height:16px;color:var(--muted)}
.f-col h5{font-size:12px;font-weight:700;color:var(--white);letter-spacing:.5px;margin-bottom:16px}
.f-item{display:flex;align-items:center;gap:10px;font-size:10px;color:var(--muted);line-height:14px;margin-bottom:14px}
.f-item .dot{width:24px;height:24px;border:1px solid #666;border-radius:50%;flex:none;display:flex;align-items:center;justify-content:center}
.f-links a{display:block;font-size:11px;color:var(--muted);text-decoration:none;line-height:20px}
</style>
</head>
<body>

<div class="abs hero-bg"></div>

<header>
  <div class="abs brand">Groovanta</div>
  <nav class="abs social" aria-label="Social networks">
    <span title="Chatterbox"></span><span title="clipwave"></span><span title="tunedrift"></span><span title="chirpnet"></span><span title="Newsletter"></span>
  </nav>
  <nav class="abs nav">
    <a class="active">HOME</a><a>BAND</a><a>ON TOUR</a><a>VIDEOS</a><a>PICS</a><a>DOWNLOADS</a><a>KONTAKT</a>
  </nav>
</header>

<div class="abs slider" role="img" aria-label="Band members on stage playing keyboards and guitar under warm lights"></div>
<div class="abs arrow-btn slider-prev"><svg width="12" height="14"><path d="M9 1 3 7l6 6" stroke="#333" stroke-width="2.5" fill="none"/></svg></div>
<div class="abs arrow-btn slider-next"><svg width="12" height="14"><path d="M3 1l6 6-6 6" stroke="#333" stroke-width="2.5" fill="none"/></svg></div>

<div class="abs welcome-bg" role="img" aria-label="Faint photo of the smiling band behind the welcome text"></div>
<section class="abs welcome">
  <h1>Welcome to <em>Groovanta</em></h1>
  <h2>A Tasty Blend of R'n'B, Funk &amp; Soul</h2>
  <p>Lorem ipsum dolor sit amet, consectetur adipiscing elit sed do eiusmod tempor incididunt ut labore et dolore magna aliqua. Ut enim ad minim veniam, quis nostrud exercitation ullamco laboris nisi ut aliquip ex ea commodo consequat. Duis aute irure dolor in reprehenderit in voluptate velit esse cillum dolore eu fugiat nulla pariatur. Excepteur sint occaecat cupidatat non proident, sunt in culpa qui officia deserunt mollit anim id est laborum sed ut perspiciatis unde omnis iste natus.</p>
  <span class="btn">Read More</span>
</section>

<h2 class="abs sec-title" style="left:70px;top:1110px">Our <em>Videos</em></h2>
<div class="abs mini-arrows" style="left:1076px;top:1118px">
  <span><svg width="8" height="10"><path d="M6 1 2 5l4 4" stroke="#333" stroke-width="2" fill="none"/></svg></span>
  <span><svg width="8" height="10"><path d="M2 1l4 4-4 4" stroke="#333" stroke-width="2" fill="none"/></svg></span>
</div>
<section class="abs videos">
  <article class="video">
    <div class="thumb" role="img" aria-label="Video still of the band on stage" style="background:linear-gradient(120deg,#5a2a10,#c0641e)">
      <svg width="44" height="44"><circle cx="22" cy="22" r="20" fill="#fff"/><path d="M17 13l12 9-12 9z" fill="#f39200"/></svg></div>
    <h3>Lorem ipsum dolor sit amet dosis good books soit amet...</h3><small>3 days ago</small>
  </article>
  <article class="video">
    <div class="thumb" role="img" aria-label="Video still of the singer in red light" style="background:linear-gradient(120deg,#8a1410,#d0361c)">
      <svg width="44" height="44"><circle cx="22" cy="22" r="20" fill="#fff"/><path d="M17 13l12 9-12 9z" fill="#f39200"/></svg></div>
    <h3>Lorem ipsum dolor sit amet dosis good books soit amet...</h3><small>3 days ago</small>
  </article>
  <article class="video">
    <div class="thumb" role="img" aria-label="Video still of the band performing" style="background:linear-gradient(120deg,#2a1a12,#7a3a1a)">
      <svg width="44" height="44"><circle cx="22" cy="22" r="20" fill="#fff"/><path d="M17 13l12 9-12 9z" fill="#f39200"/></svg></div>
    <h3>Lorem ipsum dolor sit amet dosis good books soit amet...</h3><small>3 days ago</small>
  </article>
  <article class="video">
    <div class="thumb" role="img" aria-label="Video still of the band under purple stage lights" style="background:linear-gradient(120deg,#3a1a4a,#9a3a5a)">
      <svg width="44" height="44"><circle cx="22" cy="22" r="20" fill="#fff"/><path d="M17 13l12 9-12 9z" fill="#f39200"/></svg></div>
    <h3>Lorem ipsum dolor sit amet dosis good books soit amet...</h3><small>3 days ago</small>
  </article>
</section>

<h2 class="abs sec-title" style="left:70px;top:1478px">Our <em>Music</em></h2>
<section class="abs list" style="left:70px;top:1534px">
  <div class="list-row"><div class="cover" role="img" aria-label="Band photo" style="background:linear-gradient(135deg,#5a2a14,#b0501c)"></div><div><h4>Midnight Strut - The Velvet Keys</h4><p>Lorem ipsum dolor sit amet consectetur adipiscing<br>elit sed do eiusmod tempor incididunt labore.</p></div></div>
  <div class="list-row"><div class="cover" role="img" aria-label="Band photo" style="background:linear-gradient(135deg,#7a1a12,#c83a1e)"></div><div><h4>Copper Groove - Lena Marlow</h4><p>Lorem ipsum dolor sit amet consectetur adipiscing<br>elit sed do eiusmod tempor incididunt labore.</p></div></div>
  <div class="list-row"><div class="cover" role="img" aria-label="Band photo" style="background:linear-gradient(135deg,#3a2418,#8a4a22)"></div><div><h4>Neon Shuffle - Sunday Brass</h4><p>Lorem ipsum dolor sit amet consectetur adipiscing<br>elit sed do eiusmod tempor incididunt labore.</p></div></div>
  <div class="list-row"><div class="cover" role="img" aria-label="Band photo" style="background:linear-gradient(135deg,#4a1a2a,#a2402a)"></div><div><h4>Slow Honey - Marcus Delane</h4><p>Lorem ipsum dolor sit amet consectetur adipiscing<br>elit sed do eiusmod tempor incididunt labore.</p></div></div>
</section>

<h2 class="abs sec-title" style="left:612px;top:1478px">Upcoming <em>Tour</em></h2>
<section class="abs list" style="left:612px;top:1534px">
  <div class="list-row"><div class="date"><b>25</b><i>NOV 2016</i></div><div><p class="tour-text">Lorem ipsum dolor sit amet dosis good books<br>soit amet dosis good books</p><span class="ticket">BUY TICKETS</span></div></div>
  <div class="list-row"><div class="date"><b>25</b><i>NOV 2016</i></div><div><p class="tour-text">Lorem ipsum dolor sit amet dosis good books<br>soit amet dosis good books</p><span class="ticket">BUY TICKETS</span></div></div>
  <div class="list-row"><div class="date"><b>25</b><i>NOV 2016</i></div><div><p class="tour-text">Lorem ipsum dolor sit amet dosis good books<br>soit amet dosis good books</p><span class="ticket">BUY TICKETS</span></div></div>
  <div class="list-row"><div class="date"><b>25</b><i>NOV 2016</i></div><div><p class="tour-text">Lorem ipsum dolor sit amet dosis good books<br>soit amet dosis good books</p><span class="ticket">BUY TICKETS</span></div></div>
</section>

<h2 class="abs sec-title" style="left:70px;top:2022px">Our <em>Photo Gallery</em></h2>
<section class="abs gallery">
  <div role="img" aria-label="Photo of the band on stage" style="background:linear-gradient(135deg,#241812,#6a3418)"></div>
  <div role="img" aria-label="Photo of a musician in red light" style="background:linear-gradient(135deg,#6a1410,#c8301c)"></div>
  <div role="img" aria-label="Photo of the singer on a red stage" style="background:linear-gradient(135deg,#9a1a12,#e04a1e)"></div>
  <div role="img" aria-label="Photo of the full band under purple lights" style="background:linear-gradient(135deg,#3a1848,#a83a4a)"></div>
</section>

<footer>
  <div class="abs footer"></div>
  <div class="abs f-brand">Groovanta</div>
  <p class="abs f-copy">© 2016 Groovanta. All Rights Reserved.<br>Terms of Use | Privacy Policy</p>

  <div class="abs f-col" style="left:340px;top:2330px;width:240px">
    <h5>GET IN TOUCH</h5>
    <div class="f-item"><span class="dot"><svg width="10" height="14"><path d="M5 13S1 8 1 5a4 4 0 0 1 8 0c0 3-4 8-4 8z" fill="none" stroke="#aaa"/><circle cx="5" cy="5" r="1.5" fill="#aaa"/></svg></span>12 Rhythm Lane<br>10115 Berlin</div>
    <div class="f-item"><span class="dot"><svg width="12" height="12"><path d="M2 1h3l1 3-2 1a7 7 0 0 0 3 3l1-2 3 1v3c-6 0-9-3-9-9z" fill="#aaa"/></svg></span>+49 30 555 0142</div>
    <div class="f-item"><span class="dot"><svg width="12" height="10"><rect x=".5" y=".5" width="11" height="9" fill="none" stroke="#aaa"/><path d="M1 1l5 4 5-4" fill="none" stroke="#aaa"/></svg></span>hello@groovanta.test</div>
  </div>

  <div class="abs f-col f-links" style="left:640px;top:2330px;width:180px">
    <h5>QUICK LINKS</h5>
    <a>Home</a><a>Band</a><a>On Tour</a><a>Videos</a><a>Pics</a><a>Downloads</a><a>Kontakt</a>
  </div>

  <div class="abs f-col" style="left:880px;top:2330px;width:260px">
    <h5>STAY CONNECTED</h5>
    <div class="f-item"><span class="dot"></span>Chatterbox / groovantaberlin</div>
    <div class="f-item"><span class="dot"></span>clipwave / groovantaberlin</div>
    <div class="f-item"><span class="dot"></span>tunedrift / groovantaberlin</div>
    <div class="f-item"><span class="dot"></span>chirpnet / groovantaberlin</div>
  </div>
</footer>

</body>
</html>
```